Redesign of business card for Cedar Ridge Mechanical

We are looking for a new design for our business cards for Cedar Ridge Mechanical. We are a plumbing & HVAC construction company, operating on the West Coast of Canada and USA. Logo attached.
Industry/Entity Type
Construction - Plumbing & HVAC
Contact Information for Business Card
Name, address, phone numbers, email, website address
Look and feel
Each slider illustrates characteristics of the customer's brand and the style your logo design should communicate.

```html
<!DOCTYPE html>
<html lang="en">
<head>
<meta charset="utf-8">
<title>Cedar Ridge Mechanical – Business Card</title>
<link href="https://fonts.googleapis.com/css2?family=Open+Sans:wght@400;700&display=swap" rel="stylesheet">
<style>
  :root {
    --stage: #d9d9d9;
    --card-black: #121212;
    --card-white: #ffffff;
    --ring-grey: #8e8e8e;
    --mark-dark: #2b2b2b;
    --text-light: #ffffff;
    --text-dark: #111111;
  }
  * { margin: 0; padding: 0; box-sizing: border-box; }
  html, body {
    width: 1200px; height: 913px; overflow: hidden;
    background: var(--stage);
    font-family: "Open Sans", sans-serif;
  }
  .stage { position: relative; width: 1200px; height: 913px; }

  .card {
    position: absolute;
    width: 580px; height: 330px;
    border-radius: 26px;
    background: var(--card-black);
    overflow: hidden;
    box-shadow: 0 10px 24px rgba(0,0,0,0.25);
  }
  .card-back { left: 70px; top: 90px; }
  .card-front { left: 550px; top: 490px; }

  .back-name {
    position: absolute; inset: 0;
    display: flex; align-items: center; justify-content: center;
    gap: 18px;
    color: var(--mark-dark);
    font-weight: 700; font-size: 34px; letter-spacing: 1px;
    text-transform: uppercase;
  }
  .back-name .mark-square {
    width: 30px; height: 30px; background: var(--mark-dark);
  }

  .front-art { position: absolute; inset: 0; }

  .front-name {
    position: absolute; left: 36px; top: 100px; width: 300px;
    display: flex; align-items: center; gap: 14px;
    color: var(--text-dark);
    font-weight: 700; font-size: 24px; line-height: 1.2;
    text-transform: uppercase;
  }
  .front-name .mark-square {
    flex: none; width: 26px; height: 26px; background: var(--text-dark);
  }

  .contact {
    position: absolute; left: 370px; top: 40px;
    color: var(--text-light);
    font-size: 15px; line-height: 1.3;
  }
  .contact .person { font-weight: 700; font-size: 19px; text-transform: uppercase; }
  .contact .role { margin-bottom: 22px; }
  .contact .address { margin-bottom: 22px; font-size: 16px; }
  .contact ul { list-style: none; }
  .contact li { display: flex; align-items: center; gap: 8px; margin-bottom: 3px; font-size: 16px; }
  .contact li svg { width: 13px; height: 13px; flex: none; }
</style>
</head>
<body>
<main class="stage">

  <section class="card card-back" aria-label="Card back">
    <div class="back-name"><span class="mark-square"></span>Cedar Ridge Mechanical</div>
  </section>

  <section class="card card-front" aria-label="Card front">
    <svg class="front-art" width="580" height="330" viewBox="0 0 580 330" aria-hidden="true">
      <circle cx="130" cy="190" r="228" fill="var(--ring-grey)"/>
      <circle cx="112" cy="200" r="226" fill="var(--card-black)"/>
      <circle cx="102" cy="204" r="222" fill="var(--card-white)"/>
    </svg>

    <div class="front-name"><span class="mark-square"></span>Cedar Ridge Mechanical</div>

    <div class="contact">
      <p class="person">Daniel Hayes</p>
      <p class="role">Managing Director</p>
      <p class="address">Your address, City<br>State, Zip 1234</p>
      <ul>
        <li>
          <svg viewBox="0 0 16 16"><circle cx="8" cy="8" r="8" fill="#fff"/><path d="M5 4.5l1.6 0 .7 2-1 .8a5 5 0 0 0 2.4 2.4l.8-1 2 .7v1.6c-3.8.3-6.8-2.7-6.5-6.5z" fill="#121212"/></svg>
          123 456 789
        </li>
        <li>
          <svg viewBox="0 0 16 16"><circle cx="8" cy="8" r="8" fill="#fff"/><rect x="4" y="5" width="8" height="6" fill="#121212"/><path d="M4 5l4 3.4L12 5" stroke="#fff" stroke-width="0.9" fill="none"/></svg>
          info@yourgmail.com
        </li>
        <li>
          <svg viewBox="0 0 16 16"><circle cx="8" cy="8" r="8" fill="#fff"/><circle cx="8" cy="8" r="4.5" fill="none" stroke="#121212" stroke-width="1.1"/><path d="M3.5 8h9M8 3.5c-2 2.5-2 6.5 0 9M8 3.5c2 2.5 2 6.5 0 9" stroke="#121212" stroke-width="0.9" fill="none"/></svg>
          www.yourwebsite.com
        </li>
      </ul>
    </div>
  </section>

</main>
</body>
</html>
```